Business Card Design Project

Business Card
We are rebranding with a new logo
Industry/Entity Type
Business
Contact Information for Business Card
Dennis Morvale +61 487215963 dennis@quorv.com.au P.O. Box 872 Fernlow QLD 4309
Requirements
Must have
- Logo

```html
<!DOCTYPE html>
<html lang="en">
<head>
<meta charset="utf-8">
<title>Quorv International – Business Card</title>
<link rel="stylesheet" href="https://fonts.googleapis.com/css2?family=Open+Sans:wght@700&family=Exo+2:wght@300;400&display=swap">
<style>
  :root {
    --page-bg: #e9e7e3;
    --card-white: #f4f2ee;
    --card-dark: #1f1d1d;
    --brand-blue: #1f8dbd;
    --brand-orange: #ef7d1a;
    --ink: #1c1c1c;
    --light-text: #ecebe8;
  }
  html, body {
    margin: 0;
    width: 1200px;
    height: 1200px;
    overflow: hidden;
    background: var(--page-bg);
  }
  .business-card {
    position: absolute;
    left: 75px;
    top: 300px;
    width: 1050px;
    height: 600px;
    background: var(--card-white);
    box-shadow: 0 10px 30px rgba(0,0,0,0.18);
    overflow: hidden;
  }
  .card-band {
    position: absolute;
    inset: 0;
  }
  .brand {
    position: absolute;
    left: 0;
    right: 0;
    top: 110px;
    display: flex;
    justify-content: center;
    align-items: center;
    gap: 18px;
  }
  .brand-dot {
    width: 26px;
    height: 26px;
    border-radius: 50%;
    background: var(--brand-orange);
  }
  .brand-name {
    font-family: "Open Sans", sans-serif;
    font-weight: 700;
    font-size: 44px;
    letter-spacing: 4px;
    color: var(--brand-blue);
  }
  .holder-name {
    position: absolute;
    left: 0;
    right: 0;
    top: 220px;
    text-align: center;
    font-family: "Open Sans", sans-serif;
    font-weight: 700;
    font-size: 46px;
    letter-spacing: 1px;
    color: var(--ink);
  }
  .contact {
    position: absolute;
    left: 0;
    right: 0;
    top: 455px;
    text-align: center;
    font-family: "Exo 2", sans-serif;
    font-weight: 300;
    color: var(--light-text);
    font-size: 30px;
  }
  .contact-address { margin: 0; }
  .contact-divider {
    width: 420px;
    height: 1px;
    margin: 12px auto 10px;
    background: rgba(255,255,255,0.35);
  }
  .contact-line { margin: 0; }
  .contact-sep { margin: 0 10px; }
</style>
</head>
<body>
  <div class="business-card">
    <svg class="card-band" width="1050" height="600" viewBox="0 0 1050 600" aria-hidden="true">
      <path d="M0,400 Q700,400 1050,230" fill="none" stroke="var(--card-dark)" stroke-width="6"/>
      <path d="M0,416 Q700,416 1050,246 L1050,600 L0,600 Z" fill="var(--card-dark)"/>
    </svg>

    <div class="brand">
      <span class="brand-dot"></span>
      <span class="brand-name">QUORV INTERNATIONAL</span>
    </div>

    <div class="holder-name">DENNIS MORVALE</div>

    <div class="contact">
      <p class="contact-address">P.O. Box 872, Fernlow QLD 4309</p>
      <div class="contact-divider"></div>
      <p class="contact-line">+61 487215963<span class="contact-sep">|</span>dennis@quorv.com.au</p>
    </div>
  </div>
</body>
</html>
```